Business card design for my company.
I would like the card's background colour to be black. You can also see our web site to get an idea of our brand. https://www.tmwhomecrafting.com.au/
- Name
- Email

```html
<!DOCTYPE html>
<html lang="en">
<head>
<meta charset="utf-8">
<title>TMW Home Crafting – Business Card</title>
<link rel="stylesheet" href="https://fonts.googleapis.com/css2?family=Montserrat:wght@400;500;700&display=swap">
<style>
  :root {
    --backdrop: #5c5c5c;
    --card: #222222;
    --ink: #f2f3f4;
    --green: #1e9a47;
  }
  * { margin: 0; padding: 0; box-sizing: border-box; }
  html, body {
    width: 1200px;
    height: 875px;
    overflow: hidden;
  }
  body {
    background: var(--backdrop);
    font-family: "Montserrat", sans-serif;
    color: var(--ink);
    position: relative;
  }
  .card {
    position: absolute;
    width: 540px;
    height: 310px;
    background: var(--card);
    border-radius: 18px;
  }
  .card--front { left: 40px; top: 150px; }
  .card--back { left: 620px; top: 415px; }

  .brand-name {
    display: flex;
    align-items: center;
    gap: 12px;
    font-weight: 700;
    color: var(--ink);
    letter-spacing: 0.12em;
    text-transform: uppercase;
  }
  .brand-name__mark {
    width: 14px;
    height: 14px;
    background: var(--green);
    flex: none;
  }
  .card--front .brand-name {
    position: absolute;
    left: 0; right: 0; top: 0; bottom: 0;
    justify-content: center;
    font-size: 26px;
  }
  .card--back .brand-name {
    position: absolute;
    left: 40px;
    top: 40px;
    font-size: 17px;
  }

  .person {
    position: absolute;
    left: 40px;
    top: 98px;
  }
  .person__name {
    font-size: 24px;
    font-weight: 700;
    color: var(--green);
    text-transform: uppercase;
    letter-spacing: 0.02em;
  }
  .person__role {
    font-size: 15px;
    font-weight: 400;
    margin-top: 2px;
  }
  .divider {
    position: absolute;
    left: 40px;
    top: 170px;
    width: 12px;
    height: 2px;
    background: var(--green);
  }
  .contact-list {
    position: absolute;
    left: 40px;
    top: 186px;
    list-style: none;
    font-size: 14px;
  }
  .contact-list li {
    display: flex;
    align-items: center;
    gap: 10px;
    line-height: 28px;
  }
  .contact-list svg { width: 13px; height: 13px; fill: var(--green); flex: none; }
  .accent { color: var(--green); }
</style>
</head>
<body>

  <section class="card card--front" aria-label="Card front">
    <div class="brand-name"><span class="brand-name__mark"></span>TMW Home Crafting</div>
  </section>

  <section class="card card--back" aria-label="Card back">
    <div class="brand-name"><span class="brand-name__mark"></span>TMW Home Crafting</div>

    <div class="person">
      <h1 class="person__name">Darren Hale</h1>
      <p class="person__role">CEO/Founder</p>
    </div>

    <span class="divider"></span>

    <ul class="contact-list">
      <li>
        <svg viewBox="0 0 24 24" aria-hidden="true"><path d="M6.6 10.8a15.1 15.1 0 0 0 6.6 6.6l2.2-2.2a1 1 0 0 1 1-.25 11.4 11.4 0 0 0 3.6.57 1 1 0 0 1 1 1V20a1 1 0 0 1-1 1A17 17 0 0 1 3 4a1 1 0 0 1 1-1h3.5a1 1 0 0 1 1 1c0 1.25.2 2.45.57 3.6a1 1 0 0 1-.25 1z"/></svg>
        +61 400 123 456
      </li>
      <li>
        <svg viewBox="0 0 24 24" aria-hidden="true"><path d="M2 5h20v14H2z M3 6l9 7 9-7" stroke="#222" stroke-width="1.5"/></svg>
        info@tmwhomecrafting.com.au
      </li>
      <li>
        <svg viewBox="0 0 24 24" aria-hidden="true"><circle cx="12" cy="12" r="10"/><path d="M2 12h20M12 2c3 3 3 17 0 20M12 2c-3 3-3 17 0 20" stroke="#222" stroke-width="1.3" fill="none"/></svg>
        <span>www.<span class="accent">tmwhomecrafting</span>.com.au</span>
      </li>
    </ul>
  </section>

</body>
</html>
```